Step and Repeat Backdrop for wedding reception photo booth

Would like to have a Step and Repeat Backdrop (8 foot high by 10 foot wide) that incorporates the wedding logo (attached) and the names Helen and Gavin. Background should be white, and wedding colors are burgundy and gold. Show me creativity :-) I have included some random samples.

```html
<!DOCTYPE html>
<html lang="en">
<head>
<meta charset="utf-8">
<title>Helen &amp; Gavin – Step and Repeat Backdrop</title>
<link rel="stylesheet" href="https://fonts.googleapis.com/css2?family=Playfair+Display:wght@500&display=swap">
<style>
  :root {
    --burgundy: #7d0022;
    --gold: #8b7414;
    --white: #ffffff;
    --stage: #e9e9ec;
    --flourish-on-tile: rgba(255, 255, 255, 0.38);
    --serif: "Playfair Display", Georgia, serif;
  }
  * { box-sizing: border-box; margin: 0; padding: 0; }
  html, body { width: 1200px; height: 1200px; overflow: hidden; }
  body { background: var(--stage); position: relative; font-family: var(--serif); }

  .backdrop {
    position: absolute; left: 0; top: 97px;
    width: 1200px; height: 1005px;
    background: var(--white);
  }

  .flourish-row {
    position: absolute; left: 26px;
    display: grid; grid-template-columns: repeat(10, 95px); column-gap: 22px;
  }
  .flourish-row--top { top: 17px; }
  .flourish-row--bottom { top: 952px; }
  .edge-flourish { display: block; height: 26px; border-radius: 13px; opacity: 0.45; }
  .edge-flourish--gold { background: var(--gold); }
  .edge-flourish--burgundy { background: var(--burgundy); }

  .tile-grid {
    position: absolute; left: 26px; top: 58px;
    display: grid;
    grid-template-columns: repeat(10, 95px);
    grid-template-rows: repeat(8, 95px);
    column-gap: 22px; row-gap: 17px;
  }
  .tile {
    display: flex; flex-direction: column; align-items: center; justify-content: center;
    gap: 5px; color: var(--white);
  }
  .tile--burgundy { background: var(--burgundy); }
  .tile--gold { background: var(--gold); }
  .flourish { display: block; width: 62px; height: 12px; border-radius: 6px; background: var(--flourish-on-tile); }
  .monogram { font-weight: 500; font-size: 30px; line-height: 1; letter-spacing: -1px; }

  .feature-panel {
    grid-column: 4 / 8; grid-row: 4 / 7;
    background: var(--burgundy); color: var(--white);
    display: flex; flex-direction: column; align-items: center; justify-content: center; gap: 14px;
  }
  .feature-panel .flourish { width: 290px; height: 62px; border-radius: 31px; }
  .feature-panel .monogram { font-size: 118px; letter-spacing: -4px; }
</style>
</head>
<body>
<main class="backdrop">
  <div class="flourish-row flourish-row--top">
    <i class="edge-flourish edge-flourish--gold" role="img" aria-label="Gold scroll flourish"></i>
    <i class="edge-flourish edge-flourish--burgundy" role="img" aria-label="Burgundy scroll flourish"></i>
    <i class="edge-flourish edge-flourish--gold" role="img" aria-label="Gold scroll flourish"></i>
    <i class="edge-flourish edge-flourish--burgundy" role="img" aria-label="Burgundy scroll flourish"></i>
    <i class="edge-flourish edge-flourish--gold" role="img" aria-label="Gold scroll flourish"></i>
    <i class="edge-flourish edge-flourish--burgundy" role="img" aria-label="Burgundy scroll flourish"></i>
    <i class="edge-flourish edge-flourish--gold" role="img" aria-label="Gold scroll flourish"></i>
    <i class="edge-flourish edge-flourish--burgundy" role="img" aria-label="Burgundy scroll flourish"></i>
    <i class="edge-flourish edge-flourish--gold" role="img" aria-label="Gold scroll flourish"></i>
    <i class="edge-flourish edge-flourish--burgundy" role="img" aria-label="Burgundy scroll flourish"></i>
  </div>

  <section class="tile-grid">
    <div class="feature-panel">
      <i class="flourish" role="img" aria-label="White scroll flourish with fleur-de-lis"></i>
      <span class="monogram">H&amp;G</span>
      <i class="flourish" role="img" aria-label="White scroll flourish with fleur-de-lis"></i>
    </div>

    <!-- row 1 -->
    <div class="tile tile--burgundy"><i class="flourish" role="img" aria-label="Scroll flourish"></i><span class="monogram">H&amp;G</span><i class="flourish" role="img" aria-label="Scroll flourish"></i></div>
    <div class="tile tile--gold"><i class="flourish" role="img" aria-label="Scroll flourish"></i><span class="monogram">H&amp;G</span><i class="flourish" role="img" aria-label="Scroll flourish"></i></div>
    <div class="tile tile--burgundy"><i class="flourish" role="img" aria-label="Scroll flourish"></i><span class="monogram">H&amp;G</span><i class="flourish" role="img" aria-label="Scroll flourish"></i></div>
    <div class="tile tile--gold"><i class="flourish" role="img" aria-label="Scroll flourish"></i><span class="monogram">H&amp;G</span><i class="flourish" role="img" aria-label="Scroll flourish"></i></div>
    <div class="tile tile--burgundy"><i class="flourish" role="img" aria-label="Scroll flourish"></i><span class="monogram">H&amp;G</span><i class="flourish" role="img" aria-label="Scroll flourish"></i></div>
    <div class="tile tile--gold"><i class="flourish" role="img" aria-label="Scroll flourish"></i><span class="monogram">H&amp;G</span><i class="flourish" role="img" aria-label="Scroll flourish"></i></div>
    <div class="tile tile--burgundy"><i class="flourish" role="img" aria-label="Scroll flourish"></i><span class="monogram">H&amp;G</span><i class="flourish" role="img" aria-label="Scroll flourish"></i></div>
    <div class="tile tile--gold"><i class="flourish" role="img" aria-label="Scroll flourish"></i><span class="monogram">H&amp;G</span><i class="flourish" role="img" aria-label="Scroll flourish"></i></div>
    <div class="tile tile--burgundy"><i class="flourish" role="img" aria-label="Scroll flourish"></i><span class="monogram">H&amp;G</span><i class="flourish" role="img" aria-label="Scroll flourish"></i></div>
    <div class="tile tile--gold"><i class="flourish" role="img" aria-label="Scroll flourish"></i><span class="monogram">H&amp;G</span><i class="flourish" role="img" aria-label="Scroll flourish"></i></div>
    <!-- row 2 -->
    <div class="tile tile--gold"><i class="flourish" role="img" aria-label="Scroll flourish"></i><span class="monogram">H&amp;G</span><i class="flourish" role="img" aria-label="Scroll flourish"></i></div>
    <div class="tile tile--burgundy"><i class="flourish" role="img" aria-label="Scroll flourish"></i><span class="monogram">H&amp;G</span><i class="flourish" role="img" aria-label="Scroll flourish"></i></div>
    <div class="tile tile--gold"><i class="flourish" role="img" aria-label="Scroll flourish"></i><span class="monogram">H&amp;G</span><i class="flourish" role="img" aria-label="Scroll flourish"></i></div>
    <div class="tile tile--burgundy"><i class="flourish" role="img" aria-label="Scroll flourish"></i><span class="monogram">H&amp;G</span><i class="flourish" role="img" aria-label="Scroll flourish"></i></div>
    <div class="tile tile--gold"><i class="flourish" role="img" aria-label="Scroll flourish"></i><span class="monogram">H&amp;G</span><i class="flourish" role="img" aria-label="Scroll flourish"></i></div>
    <div class="tile tile--burgundy"><i class="flourish" role="img" aria-label="Scroll flourish"></i><span class="monogram">H&amp;G</span><i class="flourish" role="img" aria-label="Scroll flourish"></i></div>
    <div class="tile tile--gold"><i class="flourish" role="img" aria-label="Scroll flourish"></i><span class="monogram">H&amp;G</span><i class="flourish" role="img" aria-label="Scroll flourish"></i></div>
    <div class="tile tile--burgundy"><i class="flourish" role="img" aria-label="Scroll flourish"></i><span class="monogram">H&amp;G</span><i class="flourish" role="img" aria-label="Scroll flourish"></i></div>
    <div class="tile tile--gold"><i class="flourish" role="img" aria-label="Scroll flourish"></i><span class="monogram">H&amp;G</span><i class="flourish" role="img" aria-label="Scroll flourish"></i></div>
    <div class="tile tile--burgundy"><i class="flourish" role="img" aria-label="Scroll flourish"></i><span class="monogram">H&amp;G</span><i class="flourish" role="img" aria-label="Scroll flourish"></i></div>
    <!-- row 3 -->
    <div class="tile tile--burgundy"><i class="flourish" role="img" aria-label="Scroll flourish"></i><span class="monogram">H&amp;G</span><i class="flourish" role="img" aria-label="Scroll flourish"></i></div>
    <div class="tile tile--gold"><i class="flourish" role="img" aria-label="Scroll flourish"></i><span class="monogram">H&amp;G</span><i class="flourish" role="img" aria-label="Scroll flourish"></i></div>
    <div class="tile tile--burgundy"><i class="flourish" role="img" aria-label="Scroll flourish"></i><span class="monogram">H&amp;G</span><i class="flourish" role="img" aria-label="Scroll flourish"></i></div>
    <div class="tile tile--gold"><i class="flourish" role="img" aria-label="Scroll flourish"></i><span class="monogram">H&amp;G</span><i class="flourish" role="img" aria-label="Scroll flourish"></i></div>
    <div class="tile tile--burgundy"><i class="flourish" role="img" aria-label="Scroll flourish"></i><span class="monogram">H&amp;G</span><i class="flourish" role="img" aria-label="Scroll flourish"></i></div>
    <div class="tile tile--gold"><i class="flourish" role="img" aria-label="Scroll flourish"></i><span class="monogram">H&amp;G</span><i class="flourish" role="img" aria-label="Scroll flourish"></i></div>
    <div class="tile tile--burgundy"><i class="flourish" role="img" aria-label="Scroll flourish"></i><span class="monogram">H&amp;G</span><i class="flourish" role="img" aria-label="Scroll flourish"></i></div>
    <div class="tile tile--gold"><i class="flourish" role="img" aria-label="Scroll flourish"></i><span class="monogram">H&amp;G</span><i class="flourish" role="img" aria-label="Scroll flourish"></i></div>
    <div class="tile tile--burgundy"><i class="flourish" role="img" aria-label="Scroll flourish"></i><span class="monogram">H&amp;G</span><i class="flourish" role="img" aria-label="Scroll flourish"></i></div>
    <div class="tile tile--gold"><i class="flourish" role="img" aria-label="Scroll flourish"></i><span class="monogram">H&amp;G</span><i class="flourish" role="img" aria-label="Scroll flourish"></i></div>
    <!-- row 4 -->
    <div class="tile tile--gold"><i class="flourish" role="img" aria-label="Scroll flourish"></i><span class="monogram">H&amp;G</span><i class="flourish" role="img" aria-label="Scroll flourish"></i></div>
    <div class="tile tile--burgundy"><i class="flourish" role="img" aria-label="Scroll flourish"></i><span class="monogram">H&amp;G</span><i class="flourish" role="img" aria-label="Scroll flourish"></i></div>
    <div class="tile tile--gold"><i class="flourish" role="img" aria-label="Scroll flourish"></i><span class="monogram">H&amp;G</span><i class="flourish" role="img" aria-label="Scroll flourish"></i></div>
    <div class="tile tile--burgundy"><i class="flourish" role="img" aria-label="Scroll flourish"></i><span class="monogram">H&amp;G</span><i class="flourish" role="img" aria-label="Scroll flourish"></i></div>
    <div class="tile tile--gold"><i class="flourish" role="img" aria-label="Scroll flourish"></i><span class="monogram">H&amp;G</span><i class="flourish" role="img" aria-label="Scroll flourish"></i></div>
    <div class="tile tile--burgundy"><i class="flourish" role="img" aria-label="Scroll flourish"></i><span class="monogram">H&amp;G</span><i class="flourish" role="img" aria-label="Scroll flourish"></i></div>
    <!-- row 5 -->
    <div class="tile tile--burgundy"><i class="flourish" role="img" aria-label="Scroll flourish"></i><span class="monogram">H&amp;G</span><i class="flourish" role="img" aria-label="Scroll flourish"></i></div>
    <div class="tile tile--gold"><i class="flourish" role="img" aria-label="Scroll flourish"></i><span class="monogram">H&amp;G</span><i class="flourish" role="img" aria-label="Scroll flourish"></i></div>
    <div class="tile tile--burgundy"><i class="flourish" role="img" aria-label="Scroll flourish"></i><span class="monogram">H&amp;G</span><i class="flourish" role="img" aria-label="Scroll flourish"></i></div>
    <div class="tile tile--gold"><i class="flourish" role="img" aria-label="Scroll flourish"></i><span class="monogram">H&amp;G</span><i class="flourish" role="img" aria-label="Scroll flourish"></i></div>
    <div class="tile tile--burgundy"><i class="flourish" role="img" aria-label="Scroll flourish"></i><span class="monogram">H&amp;G</span><i class="flourish" role="img" aria-label="Scroll flourish"></i></div>
    <div class="tile tile--gold"><i class="flourish" role="img" aria-label="Scroll flourish"></i><span class="monogram">H&amp;G</span><i class="flourish" role="img" aria-label="Scroll flourish"></i></div>
    <!-- row 6 -->
    <div class="tile tile--gold"><i class="flourish" role="img" aria-label="Scroll flourish"></i><span class="monogram">H&amp;G</span><i class="flourish" role="img" aria-label="Scroll flourish"></i></div>
    <div class="tile tile--burgundy"><i class="flourish" role="img" aria-label="Scroll flourish"></i><span class="monogram">H&amp;G</span><i class="flourish" role="img" aria-label="Scroll flourish"></i></div>
    <div class="tile tile--gold"><i class="flourish" role="img" aria-label="Scroll flourish"></i><span class="monogram">H&amp;G</span><i class="flourish" role="img" aria-label="Scroll flourish"></i></div>
    <div class="tile tile--burgundy"><i class="flourish" role="img" aria-label="Scroll flourish"></i><span class="monogram">H&amp;G</span><i class="flourish" role="img" aria-label="Scroll flourish"></i></div>
    <div class="tile tile--gold"><i class="flourish" role="img" aria-label="Scroll flourish"></i><span class="monogram">H&amp;G</span><i class="flourish" role="img" aria-label="Scroll flourish"></i></div>
    <div class="tile tile--burgundy"><i class="flourish" role="img" aria-label="Scroll flourish"></i><span class="monogram">H&amp;G</span><i class="flourish" role="img" aria-label="Scroll flourish"></i></div>
    <!-- row 7 -->
    <div class="tile tile--burgundy"><i class="flourish" role="img" aria-label="Scroll flourish"></i><span class="monogram">H&amp;G</span><i class="flourish" role="img" aria-label="Scroll flourish"></i></div>
    <div class="tile tile--gold"><i class="flourish" role="img" aria-label="Scroll flourish"></i><span class="monogram">H&amp;G</span><i class="flourish" role="img" aria-label="Scroll flourish"></i></div>
    <div class="tile tile--burgundy"><i class="flourish" role="img" aria-label="Scroll flourish"></i><span class="monogram">H&amp;G</span><i class="flourish" role="img" aria-label="Scroll flourish"></i></div>
    <div class="tile tile--gold"><i class="flourish" role="img" aria-label="Scroll flourish"></i><span class="monogram">H&amp;G</span><i class="flourish" role="img" aria-label="Scroll flourish"></i></div>
    <div class="tile tile--burgundy"><i class="flourish" role="img" aria-label="Scroll flourish"></i><span class="monogram">H&amp;G</span><i class="flourish" role="img" aria-label="Scroll flourish"></i></div>
    <div class="tile tile--gold"><i class="flourish" role="img" aria-label="Scroll flourish"></i><span class="monogram">H&amp;G</span><i class="flourish" role="img" aria-label="Scroll flourish"></i></div>
    <div class="tile tile--burgundy"><i class="flourish" role="img" aria-label="Scroll flourish"></i><span class="monogram">H&amp;G</span><i class="flourish" role="img" aria-label="Scroll flourish"></i></div>
    <div class="tile tile--gold"><i class="flourish" role="img" aria-label="Scroll flourish"></i><span class="monogram">H&amp;G</span><i class="flourish" role="img" aria-label="Scroll flourish"></i></div>
    <div class="tile tile--burgundy"><i class="flourish" role="img" aria-label="Scroll flourish"></i><span class="monogram">H&amp;G</span><i class="flourish" role="img" aria-label="Scroll flourish"></i></div>
    <div class="tile tile--gold"><i class="flourish" role="img" aria-label="Scroll flourish"></i><span class="monogram">H&amp;G</span><i class="flourish" role="img" aria-label="Scroll flourish"></i></div>
    <!-- row 8 -->
    <div class="tile tile--gold"><i class="flourish" role="img" aria-label="Scroll flourish"></i><span class="monogram">H&amp;G</span><i class="flourish" role="img" aria-label="Scroll flourish"></i></div>
    <div class="tile tile--burgundy"><i class="flourish" role="img" aria-label="Scroll flourish"></i><span class="monogram">H&amp;G</span><i class="flourish" role="img" aria-label="Scroll flourish"></i></div>
    <div class="tile tile--gold"><i class="flourish" role="img" aria-label="Scroll flourish"></i><span class="monogram">H&amp;G</span><i class="flourish" role="img" aria-label="Scroll flourish"></i></div>
    <div class="tile tile--burgundy"><i class="flourish" role="img" aria-label="Scroll flourish"></i><span class="monogram">H&amp;G</span><i class="flourish" role="img" aria-label="Scroll flourish"></i></div>
    <div class="tile tile--gold"><i class="flourish" role="img" aria-label="Scroll flourish"></i><span class="monogram">H&amp;G</span><i class="flourish" role="img" aria-label="Scroll flourish"></i></div>
    <div class="tile tile--burgundy"><i class="flourish" role="img" aria-label="Scroll flourish"></i><span class="monogram">H&amp;G</span><i class="flourish" role="img" aria-label="Scroll flourish"></i></div>
    <div class="tile tile--gold"><i class="flourish" role="img" aria-label="Scroll flourish"></i><span class="monogram">H&amp;G</span><i class="flourish" role="img" aria-label="Scroll flourish"></i></div>
    <div class="tile tile--burgundy"><i class="flourish" role="img" aria-label="Scroll flourish"></i><span class="monogram">H&amp;G</span><i class="flourish" role="img" aria-label="Scroll flourish"></i></div>
    <div class="tile tile--gold"><i class="flourish" role="img" aria-label="Scroll flourish"></i><span class="monogram">H&amp;G</span><i class="flourish" role="img" aria-label="Scroll flourish"></i></div>
    <div class="tile tile--burgundy"><i class="flourish" role="img" aria-label="Scroll flourish"></i><span class="monogram">H&amp;G</span><i class="flourish" role="img" aria-label="Scroll flourish"></i></div>
  </section>

  <div class="flourish-row flourish-row--bottom">
    <i class="edge-flourish edge-flourish--burgundy" role="img" aria-label="Burgundy scroll flourish"></i>
    <i class="edge-flourish edge-flourish--gold" role="img" aria-label="Gold scroll flourish"></i>
    <i class="edge-flourish edge-flourish--burgundy" role="img" aria-label="Burgundy scroll flourish"></i>
    <i class="edge-flourish edge-flourish--gold" role="img" aria-label="Gold scroll flourish"></i>
    <i class="edge-flourish edge-flourish--burgundy" role="img" aria-label="Burgundy scroll flourish"></i>
    <i class="edge-flourish edge-flourish--gold" role="img" aria-label="Gold scroll flourish"></i>
    <i class="edge-flourish edge-flourish--burgundy" role="img" aria-label="Burgundy scroll flourish"></i>
    <i class="edge-flourish edge-flourish--gold" role="img" aria-label="Gold scroll flourish"></i>
    <i class="edge-flourish edge-flourish--burgundy" role="img" aria-label="Burgundy scroll flourish"></i>
    <i class="edge-flourish edge-flourish--gold" role="img" aria-label="Gold scroll flourish"></i>
  </div>
</main>
</body>
</html>
```